Neatnest Home Order or Neatnest needs a business card design. Neatnest is a professi

We need a business card design that is clean, sharp and conveys a sense of organization. I already have a logo.

Target Market(s)

Families (specifically mothers), small business owners, parents, seniors

Industry/Entity Type

Business

Contact Information for Business Card

My website is www.neatnest-example.com and my Facebook page is http://www.sociallink-example.com/everyshelfsetneatly. The phone number is 418-552-7094 and I want to be listed as Lorna M. Pelham, Owner

Requirements
Must have
• My logo.

```html
<!DOCTYPE html>
<html lang="en">
<head>
<meta charset="utf-8">
<title>Neatnest — Business Card</title>
<link rel="stylesheet" href="https://fonts.googleapis.com/css2?family=Montserrat:wght@400;500;700&family=Open+Sans:wght@400;600&display=swap">
<style>
  :root {
    --page-bg: #e9e9e7;
    --card-white: #ffffff;
    --card-black: #0b0b0b;
    --brand-blue: #2f86dc;
    --band-light: #3a92e4;
    --band-deep: #1f6fc4;
    --white: #ffffff;
    --rule: rgba(255,255,255,0.7);
  }
  * { box-sizing: border-box; margin: 0; padding: 0; }
  html, body {
    width: 1200px; height: 843px; overflow: hidden;
    background: var(--page-bg);
  }
  .stage { position: relative; width: 1200px; height: 843px; }

  .card {
    position: absolute;
    width: 560px; height: 320px;
    overflow: hidden;
    box-shadow: 0 10px 30px rgba(0,0,0,0.18);
  }

  .brand {
    position: absolute;
    display: flex; align-items: center; gap: 12px;
  }
  .brand__dot {
    width: 14px; height: 14px; border-radius: 50%;
    background: var(--brand-blue);
    flex: none;
  }
  .brand__name {
    font-family: "Montserrat", sans-serif;
    font-weight: 500;
    font-size: 30px;
    letter-spacing: 6px;
    text-transform: uppercase;
    white-space: nowrap;
  }

  /* back side */
  .card--back { left: 70px; top: 70px; background: var(--card-black); }
  .card--back .brand { left: 0; right: 0; top: 118px; justify-content: center; }
  .card--back .brand__name { color: var(--white); }
  .card--back .web {
    position: absolute; left: 0; right: 0; top: 196px;
    text-align: center;
    font-family: "Montserrat", sans-serif;
    font-size: 13px; letter-spacing: 4px;
    color: var(--white);
  }

  /* front side */
  .card--front { left: 570px; top: 453px; background: var(--card-white); }
  .card--front .brand { left: 170px; top: 50px; }
  .card--front .brand__name { color: var(--brand-blue); }
  .band { position: absolute; left: 0; top: 125px; }
  .holder {
    position: absolute; left: 30px; top: 190px; width: 200px;
    text-align: right;
    color: var(--white);
  }
  .holder__name {
    font-family: "Montserrat", sans-serif;
    font-weight: 700; font-size: 17px; letter-spacing: 0.5px;
    white-space: nowrap;
  }
  .holder__role {
    font-family: "Open Sans", sans-serif;
    font-size: 13px; letter-spacing: 1px; margin-top: 4px;
  }
  .divider {
    position: absolute; left: 248px; top: 178px;
    width: 1px; height: 86px; background: var(--rule);
  }
  .contacts {
    position: absolute; left: 266px; top: 180px;
    list-style: none;
    font-family: "Open Sans", sans-serif;
    font-size: 14px; line-height: 22px;
    color: var(--white);
  }
  .contacts li { display: flex; align-items: center; gap: 8px; white-space: nowrap; }
  .contacts svg { width: 13px; height: 13px; flex: none; }
</style>
</head>
<body>
<main class="stage">

  <section class="card card--back" aria-label="Business card, back">
    <div class="brand">
      <span class="brand__dot"></span>
      <span class="brand__name">Neatnest</span>
    </div>
    <p class="web">www.neatnest-example.com</p>
  </section>

  <section class="card card--front" aria-label="Business card, front">
    <div class="brand">
      <span class="brand__dot"></span>
      <span class="brand__name">Neatnest</span>
    </div>

    <svg class="band" width="560" height="195" viewBox="0 0 560 195" aria-hidden="true">
      <defs>
        <linearGradient id="bandFill" x1="0" y1="0" x2="1" y2="1">
          <stop offset="0" stop-color="#3a92e4"/>
          <stop offset="1" stop-color="#1f6fc4"/>
        </linearGradient>
      </defs>
      <path d="M0 0 H445 A97.5 97.5 0 0 1 445 195 H0 Z" fill="url(#bandFill)"/>
    </svg>

    <div class="holder">
      <p class="holder__name">LORNA M. PELHAM</p>
      <p class="holder__role">OWNER</p>
    </div>

    <span class="divider"></span>

    <ul class="contacts">
      <li>
        <svg viewBox="0 0 24 24" aria-hidden="true"><path fill="#fff" d="M6.6 10.8a15 15 0 0 0 6.6 6.6l2.2-2.2a1 1 0 0 1 1-.25 11.4 11.4 0 0 0 3.6.57 1 1 0 0 1 1 1V20a1 1 0 0 1-1 1A17 17 0 0 1 3 4a1 1 0 0 1 1-1h3.5a1 1 0 0 1 1 1c0 1.25.2 2.45.57 3.57a1 1 0 0 1-.25 1z"/></svg>
        418-552-7094
      </li>
      <li>
        <svg viewBox="0 0 24 24" aria-hidden="true"><circle cx="12" cy="12" r="9" fill="none" stroke="#fff" stroke-width="2"/><path d="M3 12h18M12 3c3 3 3 15 0 18M12 3c-3 3-3 15 0 18" fill="none" stroke="#fff" stroke-width="1.6"/></svg>
        www.neatnest-example.com
      </li>
      <li>
        <svg viewBox="0 0 24 24" aria-hidden="true"><rect x="3" y="3" width="18" height="18" rx="2" fill="#fff"/></svg>
        neatnest.home
      </li>
    </ul>
  </section>

</main>
</body>
</html>
```